Business Card Design - Photographer

I am a landscape photographer and I require a business card design. 

I require two designs:
1)  a double sided business card
 and
b)  a single sided business card 

The single sided design can either be the same as the double sided (with just one side having all the information)....or it can be an entire new design. Its up to you.

My corporate colours are (CMYK):

Blue   69, 32, 0, 0
Grey  72,  64,  47,  31
Green  32,  2,  91,  0
Yellow   0, 19, 92, 0
Orange  0, 39, 75, 0

Colour space in final file should be in CMYK.

The details that need to be included on the card:

- Use the provided Logo
- Name: Wiktor Baranowski
- Email:   sales@vistalumeworks.com.au
- Website:    vistalumeworks.com.au
- Twitter:    twitter.com/vistalumeworks
- Facebook:   facebook.com/vistalumeworks
- Mobile  0417 539 662

Please use the attached template to design the logo to the specified size, including the marked bleed lines. I have also attached my logo in PNG (transparent background) and ai format for you to use.

The final file should be:
- Photoshop version with layers so I can edit the name/text etc. All non vector files should be high resolution at 1039 x 697 pixels at 300 dpi.

I also require a file as:
- Vector based PDF

Anyway questions please contact me.

Thank you

Industry/Entity Type

Landscape

Logo styles of interest
Pictorial/Combination Logo
Abstract Logo
Wordmark Logo
Lettermark Logo
Requirements
Must have
• The details that need to be included on the card:

- Use the provided Logo
- Name: Wiktor Baranowski
- Email: sales@vistalumeworks.com.au
- Website: vistalumeworks.com.au
- Twitter: twitter.com/vistalumeworks
- Facebook: facebook.com/vistalumeworks
- Mobile 0417 539 662

```html
<!DOCTYPE html>
<html lang="en">
<head>
<meta charset="utf-8">
<title>Vistalume Works – Business Card</title>
<link href="https://fonts.googleapis.com/css2?family=Cinzel:wght@600&family=Open+Sans:wght@400&display=swap" rel="stylesheet">
<style>
  :root {
    --page: #ecebe8;
    --card-white: #ffffff;
    --navy: #3e4354;
    --orange: #f7a548;
    --orange-back: #f8a74c;
    --text-grey: #5a5e68;
    --white: #ffffff;
  }
  * { box-sizing: border-box; margin: 0; padding: 0; }
  html, body { width: 1200px; height: 758px; overflow: hidden; }
  body { background: var(--page); position: relative; font-family: "Open Sans", sans-serif; }

  .card {
    position: absolute;
    top: 205px;
    width: 520px;
    height: 349px;
    overflow: hidden;
    box-shadow: 0 6px 18px rgba(0,0,0,0.18);
  }
  .card--front { left: 50px; background: var(--card-white); }
  .card--back { left: 630px; background: var(--orange-back); }

  /* Front */
  .band { position: absolute; left: 0; top: 0; width: 520px; height: 349px; }
  .brand {
    position: absolute; top: 22px; left: 0; width: 100%;
    display: flex; flex-direction: column; align-items: center;
  }
  .brand__dot { width: 70px; height: 70px; border-radius: 50%; background: var(--navy); }
  .brand__name {
    margin-top: 8px;
    font-family: "Cinzel", serif; font-weight: 600;
    font-size: 25px; line-height: 32px; letter-spacing: 1px; color: var(--navy);
  }
  .address {
    position: absolute; top: 158px; left: 0; width: 100%;
    text-align: center; font-size: 14px; line-height: 20px; letter-spacing: 0.8px; color: var(--text-grey);
  }
  .contacts {
    position: absolute; left: 60px; top: 240px; width: 440px;
    color: var(--white); font-size: 13.5px; line-height: 26px;
  }
  .contacts__row { display: flex; justify-content: center; align-items: center; gap: 14px; }
  .contacts__item { display: inline-flex; align-items: center; gap: 6px; }
  .icon { width: 12px; height: 12px; fill: var(--white); flex: none; }
  .icon-square { width: 11px; height: 11px; background: var(--white); flex: none; }

  /* Back */
  .back-mark {
    position: absolute; top: 52px; left: 0; width: 100%;
    display: flex; flex-direction: column; align-items: center;
  }
  .back-mark__dot { width: 150px; height: 150px; border-radius: 50%; background: var(--white); }
  .back-mark__name {
    margin-top: 16px;
    font-family: "Cinzel", serif; font-weight: 600;
    font-size: 20px; letter-spacing: 1.5px; color: var(--white);
  }
  .back-url {
    position: absolute; bottom: 40px; left: 0; width: 100%; text-align: center;
    font-family: "Cinzel", serif; font-weight: 600;
    font-size: 17px; letter-spacing: 1px; color: var(--white);
  }
</style>
</head>
<body>

<section class="card card--front">
  <svg class="band" viewBox="0 0 520 349" aria-hidden="true">
    <path d="M0,276 C150,196 380,176 520,201" fill="none" stroke="var(--orange)" stroke-width="4"/>
    <path d="M0,285 C150,205 380,185 520,210 L520,349 L0,349 Z" fill="var(--navy)"/>
  </svg>

  <div class="brand">
    <div class="brand__dot"></div>
    <div class="brand__name">VISTALUME WORKS</div>
  </div>

  <p class="address">00, Complex name, state, city 0020</p>

  <div class="contacts">
    <div class="contacts__row">
      <span class="contacts__item">
        <svg class="icon" viewBox="0 0 12 12"><rect x="3" y="0.5" width="6" height="11" rx="1.2"/></svg>
        0417 539 662
      </span>
      <span class="contacts__item">
        <svg class="icon" viewBox="0 0 12 12"><path d="M0.5,2.5 H11.5 V9.5 H0.5 Z M0.8,2.8 L6,6.8 L11.2,2.8" stroke="#3e4354" stroke-width="0.9"/></svg>
        sales@vistalumeworks.com.au
      </span>
    </div>
    <div class="contacts__row">
      <span class="contacts__item">
        <svg class="icon" viewBox="0 0 12 12"><circle cx="6" cy="6" r="5.5"/></svg>
        www.vistalumeworks.com.au
      </span>
    </div>
    <div class="contacts__row">
      <span class="contacts__item"><span class="icon-square"></span>vistalumeworks</span>
      <span class="contacts__item"><span class="icon-square"></span>vistalumeworks</span>
    </div>
  </div>
</section>

<section class="card card--back">
  <div class="back-mark">
    <div class="back-mark__dot"></div>
    <div class="back-mark__name">VISTALUME WORKS</div>
  </div>
  <p class="back-url">WWW.VISTALUMEWORKS.COM.AU</p>
</section>

</body>
</html>
```